Tech Website

1. Overview
Prism48, formally named LumoVista, is a pioneer in computer vision technology and machine learning. Based out of Santa Clara, California, Prism48 is at the forefront of the User Interface revolution; building technology architecture that grants devices with the aptitude to respond to emotional detection, gaze tracking, facial recognition, age and gender identification and gaming interaction. Winner of the Mobile Track at NOVA Founders Sprint 2012, Prism48 has developed the next generation of consumer behaviour analytics. Prism48 software solutions are scalable across various platforms including mobile phone, tablets, PC and SmartTV.
Updates

Good day, 

Please see the update to our brief - there is a PDF of the type of format and design we are looking for.  It shows each page - Landing, Technology, Product, Press and Company.

Thank you for your designs

Regards,

Target Market(s)

Target market - A mix of enterprise and consumer audiences, targeting the need for the technology in the living room space

Industry/Entity Type

Architecture

Requirements
Must have
• Design preferences - Easy to navigate, modern with sleek feel, trendy, tech saavy, using cube as a consistent element/theme. colours are not determined, but parrot green was one idea with 2 additional underlying colours. keys words like user interface revolution or sense recognition are good sources to draw inspiration.

Landing page will have a video - illustrating different uses of technology

Technical Specs - Landing page, 6 tabs/subpages, and each subpage may have 1 or 2 additional pages. Coding will be necessary, not that much at the beginning stages.

```html
<!DOCTYPE html>
<html lang="en">
<head>
<meta charset="utf-8">
<title>Prism48 – Computer Vision Technology</title>
<link rel="stylesheet" href="https://fonts.googleapis.com/css2?family=Titillium+Web:wght@400;600;700&display=swap">
<style>
  :root {
    --header-dark: #1c1c1c;
    --footer-black: #050505;
    --green-top: #a6d62a;
    --green-bottom: #7aaa0e;
    --green-divider: #c6e66e;
    --hero-top: #f4f2f3;
    --hero-bottom: #ffffff;
    --band-grey: #ebe9e7;
    --featured-bg: #f8f8f8;
    --text-dark: #444444;
    --text-mid: #555555;
    --link-blue: #2a7bc0;
    --button-dark: #111111;
    --white: #ffffff;
    --video-tone-a: #6b5a45;
    --video-tone-b: #2a2a2e;
  }
  * { margin: 0; padding: 0; box-sizing: border-box; }
  html, body { width: 1200px; height: 876px; overflow: hidden; }
  body {
    position: relative;
    font-family: "Titillium Web", "Trebuchet MS", sans-serif;
    color: var(--text-dark);
    background: var(--hero-bottom);
  }

  /* Header */
  .site-header {
    position: absolute; left: 0; top: 0; width: 1200px; height: 98px;
    background: var(--header-dark);
    z-index: 2;
  }
  .brand {
    position: absolute; left: 140px; top: 16px;
    font-size: 46px; font-weight: 600; color: var(--white); letter-spacing: -1px;
    line-height: 1.2;
  }
  .social-links {
    position: absolute; left: 955px; top: 36px; display: flex; gap: 14px;
  }
  .social-links span {
    width: 19px; height: 19px; background: #d8d8d8; border-radius: 2px; display: block;
  }
  .main-nav {
    position: absolute; left: 568px; top: 69px; width: 519px; height: 40px;
    display: flex;
    background: linear-gradient(var(--green-top), var(--green-bottom));
    border-radius: 3px 3px 0 0;
    box-shadow: 0 8px 8px -4px rgba(0,0,0,0.25);
  }
  .main-nav a {
    color: var(--white); text-decoration: none; font-weight: 600; font-size: 16px;
    display: flex; align-items: center; justify-content: center;
    border-left: 1px solid var(--green-divider);
  }
  .main-nav a:first-child { border-left: none; }

  /* Hero */
  .hero {
    position: absolute; left: 0; top: 98px; width: 1200px; height: 422px;
    background: linear-gradient(var(--hero-top), var(--hero-bottom));
    border-bottom: 2px solid #dcdcdc;
    z-index: 1;
  }
  .hero-video {
    position: absolute; left: 121px; top: 43px; width: 505px; height: 335px;
    background: var(--white); padding: 3px;
    box-shadow: 0 2px 6px rgba(0,0,0,0.3);
  }
  .hero-video .video-fill {
    width: 100%; height: 100%;
    background: radial-gradient(ellipse at 50% 45%, var(--video-tone-a), var(--video-tone-b) 75%);
    position: relative;
  }
  .hero-video .play { position: absolute; left: 197px; top: 132px; }
  .hero-title {
    position: absolute; left: 643px; top: 60px;
    font-size: 29px; font-weight: 400; color: var(--text-dark); line-height: 1.2;
  }
  .hero-copy {
    position: absolute; left: 645px; top: 108px; width: 400px;
    font-size: 16px; line-height: 20px; color: var(--text-dark);
  }
  .hero-copy p + p { margin-top: 11px; }
  .hero-copy a { color: var(--link-blue); }
  .btn-green {
    position: absolute; left: 648px; top: 233px; width: 133px; height: 36px;
    background: linear-gradient(var(--green-top), var(--green-bottom));
    color: #111; font-size: 17px; display: flex; align-items: center; justify-content: center;
    border-radius: 2px;
  }
  .btn-dark {
    position: absolute; left: 838px; width: 223px; height: 41px;
    background: linear-gradient(#2a2a2a, var(--button-dark));
    color: var(--white); display: flex; align-items: center; justify-content: center;
    border-radius: 3px; white-space: nowrap;
  }
  .btn-event { top: 288px; font-size: 16px; }
  .btn-blog { top: 337px; font-size: 17px; }
  .slide-controls { position: absolute; left: 655px; top: 334px; }

  /* Feature carousel */
  .features {
    position: absolute; left: 0; top: 522px; width: 1200px; height: 244px;
    background: var(--band-grey);
  }
  .carousel-arrow { position: absolute; top: 113px; }
  .feature-card { position: absolute; top: 57px; width: 222px; text-align: center; }
  .feature-card .frame {
    background: var(--white); padding: 6px; height: 137px;
    box-shadow: 0 1px 3px rgba(0,0,0,0.2);
  }
  .feature-card .photo { width: 100%; height: 100%; }
  .feature-card h3 {
    font-weight: 400; font-size: 17px; color: var(--text-mid); margin-top: 1px;
  }

  /* Featured in */
  .featured-in {
    position: absolute; left: 0; top: 766px; width: 1200px; height: 59px;
    background: var(--featured-bg);
  }
  .featured-in h2 {
    position: absolute; left: 139px; top: 14px; font-size: 21px; font-weight: 400; color: var(--text-mid);
  }
  .press-name {
    position: absolute; top: 16px; font-size: 19px; font-weight: 600; line-height: 28px;
    color: var(--text-mid); white-space: nowrap;
  }

  /* Footer */
  .site-footer {
    position: absolute; left: 0; top: 825px; width: 1200px; height: 51px;
    background: var(--footer-black); color: #e6e6e6; font-size: 15px;
  }
  .footer-nav { position: absolute; left: 111px; top: 13px; display: flex; gap: 17px; }
  .footer-nav a { color: #e6e6e6; text-decoration: none; }
  .copyright { position: absolute; right: 126px; top: 13px; }
</style>
</head>
<body>

<header class="site-header">
  <div class="brand">Prism48</div>
  <div class="social-links" aria-label="Social links">
    <span></span><span></span><span></span><span></span>
  </div>
  <nav class="main-nav">
    <a href="#" style="width:91px">Home</a>
    <a href="#" style="width:126px">Technology</a>
    <a href="#" style="width:102px">Product</a>
    <a href="#" style="width:85px">Press</a>
    <a href="#" style="width:115px">Company</a>
  </nav>
</header>

<section class="hero">
  <div class="hero-video">
    <div class="video-fill" role="img" aria-label="Video still: hands holding a tablet showing a hotel guide interface">
      <svg class="play" width="92" height="92" viewBox="0 0 92 92" aria-hidden="true">
        <circle cx="46" cy="46" r="45" fill="rgba(60,60,60,0.75)"/>
        <polygon points="36,28 64,46 36,64" fill="#d8d8d8"/>
      </svg>
    </div>
  </div>

  <h1 class="hero-title">Lorem ipsum dolor sit amet</h1>
  <div class="hero-copy">
    <p>Lorem ipsum dolor sit amet, consectetuer adipiscing elit, sed diam nonummy nibh euismod tincidunt ut laoreet dolore magna aliquam erat volutpat.</p>
    <p>dolore magna aliquam erat <a href="#">volutpat.</a></p>
  </div>
  <div class="btn-green">Read More</div>

  <svg class="slide-controls" width="76" height="36" viewBox="0 0 76 36" aria-label="Slide controls">
    <circle cx="17" cy="18" r="17" fill="#c9e29a"/>
    <circle cx="17" cy="18" r="13" fill="#7fae14"/>
    <polygon points="14,13 22,18 14,23" fill="#fff"/>
    <circle cx="57" cy="18" r="17" fill="#c9e29a"/>
    <circle cx="57" cy="18" r="13" fill="#7fae14"/>
    <polygon points="60,13 52,18 60,23" fill="#fff"/>
  </svg>

  <div class="btn-dark btn-event">Join Us at: EXPO 2013 Jan 8-11</div>
  <div class="btn-dark btn-blog">Subscribe to Prism48 Blog</div>
</section>

<section class="features">
  <svg class="carousel-arrow" style="left:70px" width="22" height="24" viewBox="0 0 22 24" aria-label="Previous">
    <polygon points="22,0 10,12 22,24 12,24 0,12 12,0" fill="#8cbf1a"/>
  </svg>

  <div class="feature-card" style="left:112px">
    <div class="frame"><div class="photo" role="img" aria-label="People at a trade show testing a monitor" style="background:linear-gradient(135deg,#d9dde0,#6b7a84)"></div></div>
    <h3>Gaze Detection</h3>
  </div>
  <div class="feature-card" style="left:364px">
    <div class="frame"><div class="photo" role="img" aria-label="Person gesturing at a screen showing outfits" style="background:linear-gradient(135deg,#8a6a4e,#c9a46a 60%,#3a2e28)"></div></div>
    <h3>Aptitude to Respond</h3>
  </div>
  <div class="feature-card" style="left:615px">
    <div class="frame"><div class="photo" role="img" aria-label="Hands holding a tablet running a game" style="background:linear-gradient(135deg,#e8e6e2,#2a2c30 55%,#8a7a6a)"></div></div>
    <h3>Gaming Interaction</h3>
  </div>
  <div class="feature-card" style="left:867px">
    <div class="frame"><div class="photo" role="img" aria-label="Office scene demonstrating face tracking" style="background:linear-gradient(135deg,#f1efe8,#9a8b76 60%,#4a423a)"></div></div>
    <h3>Face Recongnization</h3>
  </div>

  <svg class="carousel-arrow" style="left:1108px" width="22" height="24" viewBox="0 0 22 24" aria-label="Next">
    <polygon points="0,0 12,12 0,24 10,24 22,12 10,0" fill="#8cbf1a"/>
  </svg>
</section>

<section class="featured-in">
  <h2>As Featured In</h2>
  <span class="press-name" style="left:362px">Circuit Ledger</span>
  <span class="press-name" style="left:515px">Yodelnet</span>
  <span class="press-name" style="left:680px">Buzzframe</span>
  <span class="press-name" style="left:849px">Kestrel</span>
  <span class="press-name" style="left:945px">Dailyhour</span>
</section>

<footer class="site-footer">
  <nav class="footer-nav">
    <a href="#">Home</a><a href="#">Diensten</a><a href="#">Apps</a><a href="#">Contact</a>
  </nav>
  <div class="copyright">© Copyright Prism48. All Rights Reserved</div>
</footer>

</body>
</html>
```